I need a fresh looking, exciting and loaded design for Full service Restaurant

We need a web design for our restaurant, which offers full service Pakistani and Indian food in PA, USA. Design should be elegant, simplified so customers can navigate easily and order food online for catering as well as delivery. We need loads of pictures and room to grow. I already have a web address via vemrilo.com. It should include SSL and e-commerce for ordering food.
Be original and be creative and make it a fun site :)

```html
<!DOCTYPE html>
<html lang="en">
<head>
<meta charset="utf-8">
<title>Saffron Courtyard — Pak-Indian Cuisine</title>
<link href="https://fonts.googleapis.com/css2?family=Cabin:wght@400;500;600&family=Playball&family=Arimo:wght@400&display=swap" rel="stylesheet">
<style>
:root{
  --red:#d4171b;
  --red-dark:#9d0d10;
  --green:#1f4a12;
  --green-bright:#2d6b1a;
  --linen:#e8e8e8;
  --white:#ffffff;
  --panel:#ebebeb;
  --ink:#333333;
  --muted:#777777;
}
*{margin:0;padding:0;box-sizing:border-box}
html,body{width:1200px;height:2236px;overflow:hidden}
body{position:relative;background:var(--linen);font-family:"Arimo",Arial,sans-serif;color:var(--ink)}
.abs{position:absolute}
.column{left:85px;top:0;width:1030px;height:2160px;background:var(--white)}

/* header */
.brand{left:112px;top:34px;display:flex;align-items:center;gap:10px}
.brand-mark{width:26px;height:26px;background:var(--red)}
.brand-name{font-family:"Cabin",sans-serif;font-weight:600;font-size:27px;color:var(--red);line-height:1}
.brand-tag{left:148px;top:66px;font-size:10px;color:var(--green)}
.contact-top{top:72px;font-size:13px;color:#444;display:flex;align-items:center;gap:8px;white-space:nowrap}
.contact-top svg{width:12px;height:12px}

/* nav */
.nav{left:72px;top:113px;width:1056px;height:63px;background:var(--red);display:flex;align-items:center;justify-content:space-between;padding:0 50px 0 57px}
.nav a{font-family:"Cabin",sans-serif;font-size:15px;color:var(--white);text-decoration:none;white-space:nowrap;display:block}
.nav .sep{width:8px;height:8px;border-radius:50%;background:#fff;opacity:.8;flex:none}
.nav .current{background:var(--green);padding:8px 16px;border-radius:2px}
.fold{width:0;height:0;border-style:solid}

/* hero */
.hero{left:0;top:161px;width:1200px;height:542px;background:linear-gradient(180deg,#3a2416 0%,#5a3a22 45%,#2e1c10 100%)}
.hero-caption{left:213px;top:385px;width:775px;height:159px;background:rgba(30,18,10,.62);text-align:center;color:var(--white)}
.hero-title{font-family:"Playball",cursive;font-size:50px;margin-top:27px;line-height:1.1;white-space:nowrap}
.hero-sub{font-family:"Cabin",sans-serif;font-size:15px;margin-top:14px}
.dots{left:523px;top:552px;width:155px;height:37px;background:rgba(30,18,10,.62);display:flex;justify-content:center;align-items:center;gap:14px}
.dots span{width:15px;height:15px;border-radius:50%;background:#8a8a8a}
.dots span.on{background:var(--green-bright)}

/* feature cards */
.feature{top:641px;width:307px;height:412px}
.feature-head{position:absolute;left:0;top:0;width:307px;height:72px;background:var(--red);color:#fff;font-family:"Cabin",sans-serif;font-size:19px;display:flex;align-items:center;justify-content:center}
.feature-photo{position:absolute;left:9px;top:73px;width:289px;height:165px}
.feature-body{position:absolute;left:9px;top:238px;width:289px;height:154px;background:var(--panel);text-align:center;font-size:12.5px;line-height:31px;color:#555;padding:10px 24px 0}
.btn{position:absolute;left:74px;top:357px;width:152px;height:55px;background:var(--green);color:#fff;font-family:"Cabin",sans-serif;font-size:15px;display:flex;align-items:center;justify-content:center;gap:7px;white-space:nowrap}
.btn svg{width:14px;height:14px}

/* special menus */
.specials{left:72px;top:1098px;width:1056px;height:490px;background:var(--red)}
.specials-title{left:0;top:1136px;width:1200px;text-align:center;font-family:"Playball",cursive;font-size:52px;color:#fff}
.dish{top:1231px;width:225px;height:296px}
.dish-photo{position:absolute;left:0;top:0;width:225px;height:144px}
.dish-card{position:absolute;left:10px;top:144px;width:205px;height:152px;background:#fff;box-shadow:0 3px 6px rgba(0,0,0,.25);text-align:center;padding-top:17px}
.dish-card h3{font-family:"Cabin",sans-serif;font-weight:500;font-size:15px;color:var(--red)}
.dish-card p{font-size:11.5px;line-height:26px;color:#666;padding:6px 18px 0}

/* daily special */
.daily{left:0;top:1588px;width:1200px;height:364px;background:radial-gradient(ellipse at 50% 50%,#3a3026 0%,#1c1812 75%)}
.tag-green{left:209px;top:1650px;width:265px;height:86px;background:var(--green);transform:rotate(-5deg);color:#fff;font-family:"Cabin",sans-serif;font-size:27px;display:flex;align-items:center;justify-content:center;white-space:nowrap}
.tag-red{left:206px;top:1728px;width:503px;height:106px;background:var(--red);transform:rotate(-4deg);color:#fff;font-family:"Playball",cursive;font-size:50px;display:flex;align-items:center;justify-content:center;white-space:nowrap}
.tag-hours{left:274px;top:1818px;width:407px;height:64px;background:#fff;font-family:"Cabin",sans-serif;font-size:16px;letter-spacing:.5px;color:#333;display:flex;align-items:center;justify-content:center;white-space:nowrap}
.plate{left:712px;top:1713px;width:259px;height:149px;border-radius:50%}

/* footer */
.footer-col{top:1975px}
.footer-col h4{font-family:"Cabin",sans-serif;font-weight:400;font-size:19px;color:#333;margin-bottom:10px}
.footer-col p{font-size:11.5px;line-height:24px;color:var(--muted)}
.footer-col .line{display:flex;align-items:center;gap:8px;font-size:12px;color:#333;margin-top:8px;white-space:nowrap}
.footer-col .line svg{width:12px;height:12px;flex:none}
.vrule{top:1975px;width:0;height:160px;border-left:2px dashed #ddd}
.foot-brand{display:flex;align-items:center;gap:8px;margin-bottom:20px}
.foot-brand .brand-mark{width:18px;height:18px;background:#333}
.foot-brand .brand-name{font-size:20px;color:#333}
.bottom{left:72px;top:2160px;width:1056px;height:76px;background:var(--red);color:#fff;font-size:11.5px;display:flex;align-items:center;justify-content:space-between;padding:0 40px}
.social{display:flex;gap:5px}
.social span{width:20px;height:20px;display:block}
</style>
</head>
<body>

<div class="abs column"></div>

<!-- header -->
<div class="abs brand"><span class="brand-mark"></span><span class="brand-name">Saffron Courtyard</span></div>
<div class="abs brand-tag">A fine Pak-Indian Cuisine</div>
<div class="abs contact-top" style="left:700px">
  <svg viewBox="0 0 12 12"><path d="M6 0a4 4 0 0 0-4 4c0 3 4 8 4 8s4-5 4-8a4 4 0 0 0-4-4zm0 5.5A1.5 1.5 0 1 1 6 2.5a1.5 1.5 0 0 1 0 3z" fill="#2d6b1a"/></svg>
  Lorem Ipsm, Philadelphia, USA - 123 456
</div>
<div class="abs contact-top" style="left:977px">
  <svg viewBox="0 0 12 12"><rect width="12" height="12" rx="2" fill="#2d6b1a"/><path d="M3.5 3c.6 2.6 2.6 4.9 5 5.6l.8-1.2-1.4-.8-.6.6c-1-.5-1.8-1.3-2.3-2.4l.6-.6-.8-1.4z" fill="#fff"/></svg>
  555 0142 66310
</div>

<!-- nav -->
<div class="abs fold" style="left:72px;top:101px;border-width:0 0 12px 13px;border-color:transparent transparent var(--red-dark) transparent"></div>
<div class="abs fold" style="left:1115px;top:101px;border-width:12px 0 0 13px;border-color:transparent transparent transparent var(--red-dark)"></div>
<nav class="abs nav">
  <a class="current" href="#">Home</a><span class="sep"></span>
  <a href="#">Recipes</a><span class="sep"></span>
  <a href="#">Menu</a><span class="sep"></span>
  <a href="#">Daily Special</a><span class="sep"></span>
  <a href="#">Events</a><span class="sep"></span>
  <a href="#">About Us</a><span class="sep"></span>
  <a href="#">Contact Us</a>
</nav>

<!-- hero -->
<div class="abs hero" role="img" aria-label="Three black spoons of ground spices on a rustic wooden table"></div>
<div class="abs hero-caption">
  <div class="hero-title">Welcome To Saffron Courtyard</div>
  <div class="hero-sub">We offer full service Pakistani and Indian food in Philadelphia, USA</div>
</div>
<div class="abs dots"><span></span><span></span><span class="on"></span><span></span></div>

<!-- feature cards -->
<div class="abs feature" style="left:115px">
  <div class="feature-head">Our Menu</div>
  <div class="feature-photo" role="img" aria-label="Bowls of curry and rice" style="background:linear-gradient(135deg,#c89a3a,#8a4a14 60%,#5a3010)"></div>
  <div class="feature-body">Lorem ipsum dolor sit amet, consectetur adipiscing elit. Praesent interdum facilisis convallis.</div>
  <div class="btn"><svg viewBox="0 0 14 14"><rect y="2" width="14" height="2" fill="#fff"/><rect y="6" width="14" height="2" fill="#fff"/><rect y="10" width="14" height="2" fill="#fff"/></svg>Details</div>
</div>
<div class="abs feature" style="left:448px">
  <div class="feature-head">Make A Reservation</div>
  <div class="feature-photo" role="img" aria-label="Restaurant dining room with wooden tables" style="background:linear-gradient(180deg,#3c3c3c,#6a5036 55%,#9a6a3e)"></div>
  <div class="feature-body">Lorem ipsum dolor sit amet, consectetur adipiscing elit. Praesent interdum facilisis convallis.</div>
  <div class="btn"><svg viewBox="0 0 14 14"><rect x="1" y="2" width="12" height="11" fill="none" stroke="#fff" stroke-width="1.5"/><rect x="1" y="2" width="12" height="3" fill="#fff"/></svg>Reserve Now</div>
</div>
<div class="abs feature" style="left:781px">
  <div class="feature-head">Our History</div>
  <div class="feature-photo" role="img" aria-label="Warmly lit lounge with red chairs" style="background:linear-gradient(180deg,#4a4038,#8a6a48 50%,#7a2a20)"></div>
  <div class="feature-body">Lorem ipsum dolor sit amet, consectetur adipiscing elit. Praesent interdum facilisis convallis.</div>
  <div class="btn"><svg viewBox="0 0 14 14"><circle cx="7" cy="7" r="7" fill="#fff"/><path d="M5.5 4l3.5 3-3.5 3" fill="none" stroke="#1f4a12" stroke-width="2"/></svg>Read More</div>
</div>

<!-- special menus -->
<div class="abs fold" style="left:72px;top:1086px;border-width:0 0 12px 13px;border-color:transparent transparent var(--red-dark) transparent"></div>
<div class="abs fold" style="left:1115px;top:1086px;border-width:12px 0 0 13px;border-color:transparent transparent transparent var(--red-dark)"></div>
<div class="abs specials"></div>
<div class="abs specials-title">Special Menus</div>

<div class="abs dish" style="left:112px">
  <div class="dish-photo" role="img" aria-label="Curry in a karahi with naan" style="background:linear-gradient(135deg,#6a1a30,#b07a3a 60%,#d8c8a8)"></div>
  <div class="dish-card"><h3>Indian Mufin</h3><p>Integer lorem quam, adipiscing condim tristique, eleifend turpis. Pellentesque cursus.</p></div>
</div>
<div class="abs dish" style="left:362px">
  <div class="dish-photo" role="img" aria-label="Masala curry in a copper pot" style="background:linear-gradient(135deg,#3a2012,#a8521e 55%,#5a2a12)"></div>
  <div class="dish-card"><h3>Hot Masala</h3><p>Morbi imperdiet lacus a ipsum porttitor euismod. Proin vitae scelerisque felis.</p></div>
</div>
<div class="abs dish" style="left:612px">
  <div class="dish-photo" role="img" aria-label="Prawn curry in a pan" style="background:linear-gradient(135deg,#4a3a2a,#c8642a 55%,#6a4020)"></div>
  <div class="dish-card"><h3>Sea Food</h3><p>Cras nisi ligula, dictum ut tortor et, tempor cursus ipsum. Integer lorem quam, adipiscing.</p></div>
</div>
<div class="abs dish" style="left:862px">
  <div class="dish-photo" role="img" aria-label="Bowl of fresh peppers and vegetables" style="background:linear-gradient(135deg,#e8e0d0,#d83a1a 45%,#e8c020 75%,#5a8a2a)"></div>
  <div class="dish-card"><h3>Indian Salad</h3><p>Integer lorem quam, adipiscing condim tristique, eleifend turpis. Pellentesque cursus.</p></div>
</div>

<!-- daily special -->
<div class="abs daily" role="img" aria-label="Spices and herbs scattered on a dark table"></div>
<div class="abs tag-green">DAILY SPECIAL</div>
<div class="abs tag-red">Hot Indian Meals</div>
<div class="abs tag-hours">OPEN ALL WEEK 1ST DAY (MONDAY): 10.00 - 23.30</div>
<div class="abs plate" role="img" aria-label="Plate of spiced rice with garnish" style="background:radial-gradient(ellipse at 50% 45%,#c0702a 0%,#a8581e 45%,#f4f4f4 62%,#dcdcdc 100%)"></div>

<!-- footer -->
<div class="abs footer-col" style="left:112px;width:300px">
  <div class="foot-brand"><span class="brand-mark"></span><span class="brand-name">Saffron Courtyard</span></div>
  <p>Lorem ipsum dolor sit amet, consectetur adipiscing elit, sed do eiusmod tempor incididunt ut labore et dolore magna aliqua. Excepteur sint occaecat cupidatat non proident.</p>
</div>
<div class="abs vrule" style="left:430px"></div>
<div class="abs footer-col" style="left:451px;width:300px">
  <h4>Get In Touch</h4>
  <p>Lorem ipsum dolor sit amet, consectetur adipiscing elit, sed do eiusmod tempor incididunt ut labore.</p>
  <div class="line"><svg viewBox="0 0 12 12"><path d="M6 0a4 4 0 0 0-4 4c0 3 4 8 4 8s4-5 4-8a4 4 0 0 0-4-4zm0 5.5A1.5 1.5 0 1 1 6 2.5a1.5 1.5 0 0 1 0 3z" fill="#2d6b1a"/></svg>Lorem Ipsm, Philadelphia, USA - 123 456</div>
  <div class="line"><svg viewBox="0 0 12 12"><rect width="12" height="12" rx="2" fill="#2d6b1a"/><path d="M3.5 3c.6 2.6 2.6 4.9 5 5.6l.8-1.2-1.4-.8-.6.6c-1-.5-1.8-1.3-2.3-2.4l.6-.6-.8-1.4z" fill="#fff"/></svg>555 0142 66310</div>
</div>
<div class="abs vrule" style="left:772px"></div>
<div class="abs footer-col" style="left:793px;width:300px">
  <h4>Working Hours</h4>
  <p>Lorem ipsum dolor sit amet, consectetur adipiscing elit, sed do eiusmod tempor incididunt ut labore.</p>
  <div class="line"><svg viewBox="0 0 12 12"><circle cx="6" cy="6" r="5" fill="none" stroke="#2d6b1a" stroke-width="1.6"/><path d="M6 3v3h2.5" fill="none" stroke="#2d6b1a" stroke-width="1.4"/></svg>Mon - Fri&nbsp; 7.00 AM - 9.00 PM</div>
  <div class="line"><svg viewBox="0 0 12 12"><circle cx="6" cy="6" r="5" fill="none" stroke="#2d6b1a" stroke-width="1.6"/><path d="M6 3v3h2.5" fill="none" stroke="#2d6b1a" stroke-width="1.4"/></svg>Sat - Sun&nbsp; 7.00 AM - 12.00 PM</div>
</div>

<div class="abs fold" style="left:72px;top:2148px;border-width:0 0 12px 13px;border-color:transparent transparent var(--red-dark) transparent"></div>
<div class="abs fold" style="left:1115px;top:2148px;border-width:12px 0 0 13px;border-color:transparent transparent transparent var(--red-dark)"></div>
<footer class="abs bottom">
  <span>Copyright &nbsp;@ 2016 Saffron Courtyard. All Right Reserved.</span>
  <div class="social">
    <span style="background:#3b5998"></span>
    <span style="background:#1da1f2"></span>
    <span style="background:#dd4b39"></span>
    <span style="background:#f2a12a"></span>
  </div>
</footer>

</body>
</html>
```